Business Card Design for Property Development Company Director

I am looking for a professional and unforgettable business card design for our Director of our Property Development Company.
Please see attached .pptx file to find out what information to include. You don't have to follow the exact format shown in the file - I am interested to see your creative flair using the information provided.

```html
<!DOCTYPE html>
<html lang="en">
<head>
<meta charset="utf-8">
<title>Halvern Property Group – Business Card</title>
<link href="https://fonts.googleapis.com/css2?family=Montserrat:wght@400;500;700;800&display=swap" rel="stylesheet">
<style>
  :root{
    --bg:#3a3a3c;
    --brand-blue:#0f519b;
    --ink:#4a4a4c;
    --paper:#f5f5f6;
    --faint:#e4e6ea;
    --white:#ffffff;
  }
  *{margin:0;padding:0;box-sizing:border-box}
  html,body{width:1200px;height:1021px;overflow:hidden;background:var(--bg);font-family:'Montserrat',sans-serif}
  .stage{position:relative;width:1200px;height:1021px}
  .card{position:absolute;left:300px;width:600px;height:343px;overflow:hidden;box-shadow:0 12px 28px rgba(0,0,0,.45)}

  /* Back */
  .card--back{top:100px;background:var(--brand-blue);color:var(--white)}
  .back-brand{position:absolute;left:0;right:0;top:112px;display:flex;justify-content:center;align-items:center;gap:18px}
  .brand-square{width:52px;height:52px;background:currentColor}
  .wordmark{font-weight:700;line-height:1}
  .wordmark__name{display:block;font-size:44px;letter-spacing:1px}
  .wordmark__sub{display:block;font-size:13px;letter-spacing:6.5px;margin-top:4px}
  .back-tagline{position:absolute;left:0;right:0;bottom:34px;text-align:center;font-size:13px;letter-spacing:.5px}
  .back-tagline strong{font-weight:700}

  /* Front */
  .card--front{top:540px;background:var(--paper)}
  .front-brand{position:absolute;left:34px;top:34px;display:flex;align-items:center;gap:12px;color:var(--brand-blue)}
  .front-brand .brand-square{width:40px;height:40px}
  .front-brand .wordmark__name{font-size:33px}
  .front-brand .wordmark__sub{font-size:10px;letter-spacing:5px}
  .faint-block{position:absolute;right:-30px;top:120px;width:240px;height:260px;background:var(--faint)}
  .rule{position:absolute;left:34px;right:34px;height:1px;background:var(--ink)}
  .rule--top{top:150px}
  .rule--bottom{top:238px;left:340px}
  .contacts{position:absolute;left:34px;top:166px;list-style:none;color:var(--ink);font-size:14px;line-height:21px}
  .contacts li{display:flex;align-items:center;gap:8px}
  .contacts svg{width:13px;height:13px;fill:var(--brand-blue)}
  .contacts .licence{margin-top:2px}
  .person{position:absolute;right:40px;top:180px;text-align:right}
  .person__name{font-weight:800;font-size:21px;color:var(--brand-blue);letter-spacing:.5px}
  .person__role{font-weight:500;font-size:14px;color:var(--ink);letter-spacing:1px}
  .band{position:absolute;left:0;right:0;bottom:0;height:50px;background:var(--brand-blue);color:var(--white);font-size:15px;font-weight:500;display:flex;align-items:center;padding-left:100px;letter-spacing:.4px}
</style>
</head>
<body>
<main class="stage">
  <section class="card card--back">
    <div class="back-brand">
      <span class="brand-square"></span>
      <span class="wordmark"><span class="wordmark__name">HALVERN</span><span class="wordmark__sub">PROPERTY GROUP</span></span>
    </div>
    <p class="back-tagline">Ask me about our <strong>INVESTMENT &amp; PARTNERSHIP</strong> opportunities</p>
  </section>

  <section class="card card--front">
    <div class="faint-block"></div>
    <div class="front-brand">
      <span class="brand-square"></span>
      <span class="wordmark"><span class="wordmark__name">HALVERN</span><span class="wordmark__sub">PROPERTY GROUP</span></span>
    </div>
    <div class="rule rule--top"></div>
    <ul class="contacts">
      <li><svg viewBox="0 0 24 24"><path d="M6.6 10.8a15.1 15.1 0 006.6 6.6l2.2-2.2c.3-.3.7-.4 1-.2 1.1.4 2.3.6 3.6.6.6 0 1 .4 1 1V20c0 .6-.4 1-1 1A17 17 0 013 4c0-.6.4-1 1-1h3.5c.6 0 1 .4 1 1 0 1.3.2 2.5.6 3.6.1.3 0 .7-.2 1z"/></svg>0400 318 762</li>
      <li><svg viewBox="0 0 24 24"><path d="M2 5h20v14H2zm2 2v.5l8 5 8-5V7zm0 2.8V17h16V9.8l-8 5z"/></svg>daniel@halvern.com.au</li>
      <li><svg viewBox="0 0 24 24"><path d="M12 2a10 10 0 100 20 10 10 0 000-20zm0 2c.9 1.2 1.6 2.7 2 4h-4c.4-1.3 1.1-2.8 2-4zM4.3 14a8 8 0 010-4h3.4a16 16 0 000 4zm.9 2h3c.3 1.3.8 2.5 1.4 3.6A8 8 0 015.2 16zM8.2 8h-3a8 8 0 014.4-3.6C9 5.5 8.5 6.7 8.2 8zM12 20c-.9-1.2-1.6-2.7-2-4h4c-.4 1.3-1.1 2.8-2 4zm2.3-6H9.7a14 14 0 010-4h4.6a14 14 0 010 4zm.1 5.6c.6-1.1 1.1-2.3 1.4-3.6h3a8 8 0 01-4.4 3.6zm1.9-5.6a16 16 0 000-4h3.4a8 8 0 010 4zm-.5-6c-.3-1.3-.8-2.5-1.4-3.6A8 8 0 0118.8 8z"/></svg>www.halvern.com.au</li>
      <li class="licence">Real Estate Lic: 5129634 &amp; 5129635</li>
    </ul>
    <div class="person">
      <p class="person__name">DANIEL MERCER</p>
      <p class="person__role">DIRECTOR</p>
    </div>
    <div class="rule rule--bottom"></div>
    <div class="band">Property Development &amp; Site Acquisition Specialists</div>
  </section>
</main>
</body>
</html>
```